Radio Service company needs ad for trade publication

Airwave Allies provides sales, content, production, technology, and promotion products and services to radio stations to help increase sales and solutions to improve operations and reduce costs. We are looking for a creative ad (sizes 720x250, 300x250, 728x180) with a theme around "MASTER YOUR 2024 BUDGET with AIRWAVE ALLIES". Categories we have products/services to help them get budget into alignment. (1) Sales (2) Content & Programming (3) Technology (4) Production & Imaging (5) Promotions & Marketing (6) Support Services
"Don't go into the new year with an Unrealistic Budget.....We can Help!"

```html
<!DOCTYPE html>
<html lang="en">
<head>
<meta charset="utf-8">
<title>Airwave Allies – 2024 Budget Ad Set</title>
<link href="https://fonts.googleapis.com/css2?family=Anton&family=Poppins:wght@400;500;600;700&display=swap" rel="stylesheet">
<style>
  :root{
    --sky:#22a3f1;
    --navy:#2a3d90;
    --navy-deep:#213479;
    --white:#ffffff;
    --bar:#1c9ef2;
    --arrow:#27ae4a;
    --gold:#f9bd26;
    --gold-ink:#2b1f00;
    --brand:#1f86de;
    --tag:#1e9bf0;
  }
  *{box-sizing:border-box;margin:0;padding:0}
  html,body{width:686px;height:1200px;overflow:hidden;background:var(--sky)}
  .stage{position:relative;width:800px;height:1400px;transform:scale(.8575);transform-origin:0 0}

  .ad{position:absolute;overflow:hidden;color:var(--white);
      background:linear-gradient(135deg,var(--navy) 0%,var(--navy-deep) 100%);
      box-shadow:0 12px 20px rgba(0,0,0,.35);font-family:"Poppins",sans-serif}
  .ad--wide{width:720px;height:250px}
  .ad--slim{width:724px;height:180px}
  .ad--square{width:336px;height:280px}

  .headline{position:absolute;font-family:"Anton",sans-serif;text-transform:uppercase;line-height:.9;letter-spacing:.5px}
  .headline span{display:block}
  .headline .with-tag{position:absolute;background:var(--tag);color:#111;font-size:14px;line-height:1;padding:3px 10px;transform:rotate(-8deg)}

  .ad--wide .headline{left:16px;top:30px}
  .ad--wide .verb{font-size:70px}
  .ad--wide .sub{font-size:25px;margin-top:2px}
  .ad--wide .name-1{font-size:68px;margin-top:8px}
  .ad--wide .name-2{font-size:48px;margin-top:2px}
  .ad--wide .with-tag{left:92px;top:106px}

  .ad--slim .headline{left:42px;top:14px}
  .ad--slim .verb{font-size:50px}
  .ad--slim .sub{font-size:19px;margin-top:2px}
  .ad--slim .name-1{font-size:52px;margin-top:6px}
  .ad--slim .name-2{font-size:36px;margin-top:1px}
  .ad--slim .with-tag{left:68px;top:62px;font-size:11px;padding:2px 8px}

  .ad--square .headline{left:17px;top:22px}
  .ad--square .verb{font-size:46px}
  .ad--square .sub{font-size:18px;margin-top:2px}
  .ad--square .name-1{font-size:48px;margin-top:5px}
  .ad--square .name-2{font-size:33px;margin-top:1px}
  .ad--square .with-tag{left:70px;top:58px;font-size:11px;padding:2px 8px}

  .divider{position:absolute;background:var(--white)}
  .ad--wide .divider{left:276px;top:38px;width:2px;height:180px}
  .ad--slim .divider{left:240px;top:24px;width:2px;height:140px}
  .ad--square .divider{left:17px;top:178px;width:158px;height:2px}

  .pitch{position:absolute}
  .pitch h3{font-weight:700;font-size:15px;letter-spacing:-.2px;margin-bottom:4px}
  .pitch ul{list-style:none}
  .pitch li{position:relative;padding-left:16px;font-weight:500;font-size:14px;line-height:21px}
  .pitch li::before{content:"";position:absolute;left:0;top:4px;border-left:9px solid var(--tag);border-top:6px solid transparent;border-bottom:6px solid transparent}
  .ad--wide .pitch{left:286px;top:32px}
  .ad--slim .pitch{left:250px;top:16px}
  .ad--slim .pitch h3{margin-bottom:2px;line-height:20px}
  .ad--slim .pitch li{font-size:14.5px;line-height:20px}
  .ad--slim .pitch li::before{top:3px}
  .ad--square .pitch{left:17px;top:186px}
  .ad--square .pitch li{font-size:14.5px;line-height:22px}

  .offer{position:absolute;background:var(--gold)}
  .offer strong{color:var(--gold-ink);font-weight:700}
  .offer .offer-body{color:var(--white)}
  .ad--wide .offer{left:286px;top:121px;width:250px;height:107px;padding:4px 10px;line-height:1.15}
  .ad--wide .offer .offer-head{display:block;font-size:18px}
  .ad--wide .offer .offer-body{display:block;font-size:17.5px}
  .ad--wide .offer .offer-cta{display:block;font-size:11px;margin-top:2px}
  .ad--slim .offer{left:255px;top:110px;width:295px;height:50px;text-align:center;padding:3px 6px;line-height:1.1;overflow:hidden}
  .ad--slim .offer .offer-head{color:var(--white);font-size:11.5px}
  .ad--slim .offer .offer-body{font-size:11.5px}
  .ad--slim .offer .offer-cta{display:block;font-size:13.5px;line-height:1.15;margin-top:1px}

  .brand-corner{position:absolute;top:0;right:0;background:var(--white);border-bottom-left-radius:100% 100%;
      display:flex;align-items:flex-start;justify-content:flex-end}
  .brand-corner .brand-name{color:var(--brand);font-weight:700;line-height:1.05;text-align:center;text-transform:uppercase}
  .ad--wide .brand-corner{width:150px;height:128px;padding:22px 10px 0 0}
  .ad--wide .brand-name{font-size:19px}
  .ad--slim .brand-corner{width:146px;height:86px;padding:16px 10px 0 0}
  .ad--slim .brand-name{font-size:18px}
  .ad--square .brand-corner{width:148px;height:88px;padding:18px 12px 0 0}
  .ad--square .brand-name{font-size:18px}

  .growth-chart{position:absolute}
  .ad--wide .growth-chart{left:545px;top:72px;width:160px;height:160px}
  .ad--slim .growth-chart{left:563px;top:52px;width:120px;height:120px}
  .ad--square .growth-chart{left:208px;top:58px;width:122px;height:122px}
</style>
</head>
<body>
<main class="stage">

  <section class="ad ad--wide" style="left:40px;top:52px">
    <h2 class="headline"><span class="verb">Balance</span><span class="sub">Your 2024 Budget</span><span class="name-1">Airwave</span><span class="name-2">Allies</span><em class="with-tag">With</em></h2>
    <div class="divider"></div>
    <div class="pitch"><h3>SOLUTIONS FOR BROADCASTERS</h3><ul><li>Need to Improve Your Cash Flow?</li><li>Need to Streamline Your Expenses?</li><li>Need more Non-Traditional Revenue?</li></ul></div>
    <p class="offer"><strong class="offer-head">START SAVINGS NOW!</strong><span class="offer-body">Packages are available with no payments until year 2025</span><strong class="offer-cta">CLICK HERE TO CONTACT US TODAY!</strong></p>
    <div class="brand-corner"><span class="brand-name">Airwave<br>Allies</span></div>
    <svg class="growth-chart" viewBox="0 0 160 160" aria-hidden="true"><g fill="var(--bar)"><rect x="0" y="115" width="24" height="45"/><rect x="30" y="103" width="24" height="57"/><rect x="60" y="88" width="24" height="72"/><rect x="90" y="70" width="24" height="90"/><rect x="120" y="50" width="24" height="110"/></g><polyline points="4,88 44,66 68,76 132,22" fill="none" stroke="var(--arrow)" stroke-width="10" stroke-linejoin="round"/><polygon points="116,12 158,0 148,42" fill="var(--arrow)"/></svg>
  </section>

  <section class="ad ad--wide" style="left:40px;top:328px">
    <h2 class="headline"><span class="verb">Build</span><span class="sub">Your 2024 Budget</span><span class="name-1">Airwave</span><span class="name-2">Allies</span><em class="with-tag">With</em></h2>
    <div class="divider"></div>
    <div class="pitch"><h3>SOLUTIONS FOR BROADCASTERS</h3><ul><li>Need to Improve Your Cash Flow?</li><li>Need to Streamline Your Expenses?</li><li>Need more Non-Traditional Revenue?</li></ul></div>
    <p class="offer"><strong class="offer-head">START SAVINGS NOW!</strong><span class="offer-body">Packages are available with no payments until year 2025</span><strong class="offer-cta">CLICK HERE TO CONTACT US TODAY!</strong></p>
    <div class="brand-corner"><span class="brand-name">Airwave<br>Allies</span></div>
    <svg class="growth-chart" viewBox="0 0 160 160" aria-hidden="true"><g fill="var(--bar)"><rect x="0" y="115" width="24" height="45"/><rect x="30" y="103" width="24" height="57"/><rect x="60" y="88" width="24" height="72"/><rect x="90" y="70" width="24" height="90"/><rect x="120" y="50" width="24" height="110"/></g><polyline points="4,88 44,66 68,76 132,22" fill="none" stroke="var(--arrow)" stroke-width="10" stroke-linejoin="round"/><polygon points="116,12 158,0 148,42" fill="var(--arrow)"/></svg>
  </section>

  <section class="ad ad--slim" style="left:38px;top:605px">
    <h2 class="headline"><span class="verb">Balance</span><span class="sub">Your 2024 Budget</span><span class="name-1">Airwave</span><span class="name-2">Allies</span><em class="with-tag">With</em></h2>
    <div class="divider"></div>
    <div class="pitch"><h3>SOLUTIONS FOR BROADCASTERS</h3><ul><li>Need to Improve Your Cash Flow?</li><li>Need to Streamline Your Expenses?</li><li>Need more Non-Traditional Revenue?</li></ul></div>
    <p class="offer"><strong class="offer-head">START SAVINGS NOW!</strong> <span class="offer-body">Packages are available with no payments until year 2025</span><strong class="offer-cta">CLICK HERE TO CONTACT US TODAY!</strong></p>
    <div class="brand-corner"><span class="brand-name">Airwave<br>Allies</span></div>
    <svg class="growth-chart" viewBox="0 0 160 160" aria-hidden="true"><g fill="var(--bar)"><rect x="0" y="115" width="24" height="45"/><rect x="30" y="103" width="24" height="57"/><rect x="60" y="88" width="24" height="72"/><rect x="90" y="70" width="24" height="90"/><rect x="120" y="50" width="24" height="110"/></g><polyline points="4,88 44,66 68,76 132,22" fill="none" stroke="var(--arrow)" stroke-width="10" stroke-linejoin="round"/><polygon points="116,12 158,0 148,42" fill="var(--arrow)"/></svg>
  </section>

  <section class="ad ad--slim" style="left:36px;top:818px;width:726px">
    <h2 class="headline"><span class="verb">Build</span><span class="sub">Your 2024 Budget</span><span class="name-1">Airwave</span><span class="name-2">Allies</span><em class="with-tag">With</em></h2>
    <div class="divider"></div>
    <div class="pitch"><h3>SOLUTIONS FOR BROADCASTERS</h3><ul><li>Need to Improve Your Cash Flow?</li><li>Need to Streamline Your Expenses?</li><li>Need more Non-Traditional Revenue?</li></ul></div>
    <p class="offer"><strong class="offer-head">START SAVINGS NOW!</strong> <span class="offer-body">Packages are available with no payments until year 2025</span><strong class="offer-cta">CLICK HERE TO CONTACT US TODAY!</strong></p>
    <div class="brand-corner"><span class="brand-name">Airwave<br>Allies</span></div>
    <svg class="growth-chart" viewBox="0 0 160 160" aria-hidden="true"><g fill="var(--bar)"><rect x="0" y="115" width="24" height="45"/><rect x="30" y="103" width="24" height="57"/><rect x="60" y="88" width="24" height="72"/><rect x="90" y="70" width="24" height="90"/><rect x="120" y="50" width="24" height="110"/></g><polyline points="4,88 44,66 68,76 132,22" fill="none" stroke="var(--arrow)" stroke-width="10" stroke-linejoin="round"/><polygon points="116,12 158,0 148,42" fill="var(--arrow)"/></svg>
  </section>

  <section class="ad ad--square" style="left:40px;top:1028px">
    <h2 class="headline"><span class="verb">Balance</span><span class="sub">Your 2024 Budget</span><span class="name-1">Airwave</span><span class="name-2">Allies</span><em class="with-tag">With</em></h2>
    <div class="divider"></div>
    <div class="pitch"><h3>SOLUTIONS FOR BROADCASTERS</h3><ul><li>Need to Improve Your Cash Flow?</li><li>Need to Streamline Your Expenses?</li><li>Need more Non-Traditional Revenue?</li></ul></div>
    <div class="brand-corner"><span class="brand-name">Airwave<br>Allies</span></div>
    <svg class="growth-chart" viewBox="0 0 160 160" aria-hidden="true"><g fill="var(--bar)"><rect x="0" y="115" width="24" height="45"/><rect x="30" y="103" width="24" height="57"/><rect x="60" y="88" width="24" height="72"/><rect x="90" y="70" width="24" height="90"/><rect x="120" y="50" width="24" height="110"/></g><polyline points="4,88 44,66 68,76 132,22" fill="none" stroke="var(--arrow)" stroke-width="10" stroke-linejoin="round"/><polygon points="116,12 158,0 148,42" fill="var(--arrow)"/></svg>
  </section>

  <section class="ad ad--square" style="left:402px;top:1028px;width:334px">
    <h2 class="headline"><span class="verb">Build</span><span class="sub">Your 2024 Budget</span><span class="name-1">Airwave</span><span class="name-2">Allies</span><em class="with-tag">With</em></h2>
    <div class="divider"></div>
    <div class="pitch"><h3>SOLUTIONS FOR BROADCASTERS</h3><ul><li>Need to Improve Your Cash Flow?</li><li>Need to Streamline Your Expenses?</li><li>Need more Non-Traditional Revenue?</li></ul></div>
    <div class="brand-corner"><span class="brand-name">Airwave<br>Allies</span></div>
    <svg class="growth-chart" viewBox="0 0 160 160" aria-hidden="true"><g fill="var(--bar)"><rect x="0" y="115" width="24" height="45"/><rect x="30" y="103" width="24" height="57"/><rect x="60" y="88" width="24" height="72"/><rect x="90" y="70" width="24" height="90"/><rect x="120" y="50" width="24" height="110"/></g><polyline points="4,88 44,66 68,76 132,22" fill="none" stroke="var(--arrow)" stroke-width="10" stroke-linejoin="round"/><polygon points="116,12 158,0 148,42" fill="var(--arrow)"/></svg>
  </section>

</main>
</body>
</html>
```